Realtor branding business card

modern, simple and self branding. Broker office logo needs to be used but not emphasized. Looking to brand myself

Target Market(s)

buyers, sellers and investors

Industry/Entity Type

Realtor

Contact Information for Business Card

Sample of my current business card on file

Requirements
Must have
• my website - tobiasmerrowkl.com
• Realtor logo
• Fair housing logo
Nice to have
• Colors from office logo but not a must
Should not have
• Do not want headshot

```html
<!DOCTYPE html>
<html lang="en">
<head>
<meta charset="utf-8">
<title>Tobias Merrow – Business Card</title>
<link href="https://fonts.googleapis.com/css2?family=Roboto:wght@400;500;700&display=swap" rel="stylesheet">
<style>
  :root {
    --navy: #271670;
    --navy-light: #35237a;
    --red: #d9261c;
    --band: #f1f1f5;
    --text: #4a4a4a;
    --white: #ffffff;
    --backdrop: #e4e4e4;
  }
  * { margin: 0; padding: 0; box-sizing: border-box; }
  html, body { width: 1125px; height: 1200px; overflow: hidden; }
  body { background: var(--backdrop); font-family: "Roboto", sans-serif; position: relative; }

  .card {
    position: absolute;
    left: 171px;
    width: 800px;
    height: 457px;
    transform: scale(1.0325);
    transform-origin: top left;
    overflow: hidden;
  }
  .card--front { top: 106px; background: var(--white); }
  .card--back { top: 639px; background: var(--navy); }
  .card__shapes { position: absolute; inset: 0; width: 800px; height: 457px; }

  .brand { position: absolute; left: 57px; top: 70px; display: flex; align-items: flex-start; gap: 10px; font-weight: 700; line-height: 1; }
  .brand__mark { width: 18px; height: 18px; background: var(--red); margin-top: 8px; }
  .brand__name { font-size: 50px; letter-spacing: -1px; }
  .brand__sub { font-size: 24px; margin-top: 6px; }
  .card--front .brand { color: var(--navy); }
  .card--back .brand { color: var(--white); }

  .contact { position: absolute; left: 57px; top: 246px; color: var(--text); font-size: 19px; line-height: 25px; }
  .contact__list { list-style: none; margin-top: 14px; }
  .contact__item { display: flex; align-items: center; gap: 10px; }
  .contact__icon { width: 20px; height: 20px; fill: var(--navy); }

  .agent { position: absolute; right: 66px; top: 245px; text-align: right; }
  .agent__name { font-size: 29px; font-weight: 700; color: var(--navy); line-height: 1.1; }
  .agent__title { font-size: 20px; font-weight: 500; color: var(--red); }

  .website { position: absolute; right: 68px; top: 418px; color: var(--white); font-size: 19px; letter-spacing: 0.2px; }

  .badges { position: absolute; left: 55px; top: 342px; display: flex; gap: 12px; }
  .badge { width: 44px; height: 56px; background: var(--white); }
  .badge--round { border-radius: 4px; width: 60px; }
</style>
</head>
<body>

<section class="card card--front" aria-label="Business card front">
  <svg class="card__shapes" viewBox="0 0 800 457" aria-hidden="true">
    <polygon points="220,457 590,0 800,0 800,80 465,457" fill="var(--band)"/>
    <polygon points="530,457 800,115 800,360 720,457" fill="var(--band)"/>
    <polygon points="464,407 800,407 800,457 424,457" fill="var(--navy)"/>
    <polygon points="762,276 800,245 800,309" fill="var(--red)"/>
  </svg>

  <div class="brand">
    <span class="brand__mark"></span>
    <div>
      <div class="brand__name">Brightway</div>
      <div class="brand__sub">Realty Group</div>
    </div>
  </div>

  <div class="contact">
    <p>480 Harbor Lane Dr.<br>Lakeview Springs, FL 32000</p>
    <ul class="contact__list">
      <li class="contact__item">
        <svg class="contact__icon" viewBox="0 0 24 24"><path d="M6.6 10.8c1.4 2.8 3.8 5.1 6.6 6.6l2.2-2.2c.3-.3.7-.4 1-.2 1.1.4 2.3.6 3.6.6.6 0 1 .4 1 1V20c0 .6-.4 1-1 1C10.6 21 3 13.4 3 4c0-.6.4-1 1-1h3.5c.6 0 1 .4 1 1 0 1.3.2 2.5.6 3.6.1.3 0 .7-.2 1z"/></svg>
        <span>555.210.4000</span>
      </li>
      <li class="contact__item">
        <svg class="contact__icon" viewBox="0 0 24 24"><path d="M7 2h10a2 2 0 0 1 2 2v16a2 2 0 0 1-2 2H7a2 2 0 0 1-2-2V4a2 2 0 0 1 2-2zm0 3v13h10V5zm5 14.2a1 1 0 1 0 0 .1z"/></svg>
        <span>555.318.7742</span>
      </li>
      <li class="contact__item">
        <svg class="contact__icon" viewBox="0 0 24 24"><path d="M3 6h18v12H3zm2 2v.4l7 4.4 7-4.4V8l-7 4.4z"/></svg>
        <span>merrowrealty@mailbox.com</span>
      </li>
    </ul>
  </div>

  <div class="agent">
    <div class="agent__name">Tobias Merrow, PA</div>
    <div class="agent__title">Realtor</div>
  </div>

  <div class="website">www.tobiasmerrowkl.com</div>
</section>

<section class="card card--back" aria-label="Business card back">
  <svg class="card__shapes" viewBox="0 0 800 457" aria-hidden="true">
    <polygon points="220,457 590,0 800,0 800,80 465,457" fill="var(--navy-light)"/>
    <polygon points="530,457 800,115 800,360 720,457" fill="var(--navy-light)"/>
    <polygon points="464,407 800,407 800,457 424,457" fill="var(--red)"/>
  </svg>

  <div class="brand">
    <span class="brand__mark"></span>
    <div>
      <div class="brand__name">Brightway</div>
      <div class="brand__sub">Realty Group</div>
    </div>
  </div>

  <div class="badges">
    <div class="badge" role="img" aria-label="Realtor association badge"></div>
    <div class="badge badge--round" role="img" aria-label="Equal housing opportunity badge"></div>
  </div>

  <div class="website">www.tobiasmerrowkl.com</div>
</section>

</body>
</html>
```